Super elegant, crisp & clean Business card design required

We recently upgraded our branding - which is on our website - talvendoraphoto.com

I would like a simple, yet elegant, clean business card design please.

The font of my logo is Cinzel - and because of the natural colour - it's best to have this on a black background.

I would like to have the back of the business card - with simply my logo.

PLEASE DO NOT SUBMIT A COMPLICATED / UNCLEAN DESIGN

Industry/Entity Type

Business

Contact Information for Business Card

Talven Doroshko Photography

Font styles to use
Other font styles liked:
• Cinzel

Requirements
Must have
• A backpage with nothing but my logo
• Simple design - stands out
Should not have
• Colour that dont align with my logo
• Over complicated '/ non symmetrical design

```html
<!DOCTYPE html>
<html lang="en">
<head>
<meta charset="utf-8">
<title>Talven Doroshko Photography – Business Card</title>
<link rel="stylesheet" href="https://fonts.googleapis.com/css2?family=Cinzel:wght@400;500&family=Arimo:wght@400&display=swap">
<style>
  :root {
    --backdrop: #d9d4cb;
    --card: #fbfbfa;
    --taupe: #8b7d66;
    --ink: #1f1f1f;
    --icon-fill: #ffffff;
  }
  * { box-sizing: border-box; margin: 0; padding: 0; }
  html, body {
    width: 1200px; height: 892px; overflow: hidden;
    background: var(--backdrop);
  }
  .stage {
    position: relative; width: 1200px; height: 892px;
    display: flex; align-items: center; justify-content: center; gap: 40px;
  }
  .card {
    position: relative; width: 540px; height: 309px;
    background: var(--card);
    box-shadow: 0 2px 10px rgba(0,0,0,0.12);
  }

  /* Back: brand name only */
  .card-back {
    display: flex; flex-direction: column; align-items: center; justify-content: center;
  }
  .brand-mark {
    width: 64px; height: 64px; border-radius: 50%;
    border: 2px solid var(--taupe); margin-bottom: 22px;
  }
  .brand-name {
    font-family: "Cinzel", serif; font-weight: 400; color: var(--taupe);
    font-size: 34px; letter-spacing: 0.5px; line-height: 1;
  }
  .brand-sub {
    font-family: "Cinzel", serif; font-weight: 400; color: var(--taupe);
    font-size: 15px; letter-spacing: 11px; margin-top: 8px; padding-left: 11px;
  }

  /* Front: brand + contact */
  .card-front .front-brand {
    position: absolute; left: 34px; top: 44px;
    display: flex; flex-direction: column; align-items: center;
  }
  .card-front .brand-mark { width: 44px; height: 44px; margin-bottom: 12px; }
  .card-front .brand-name { font-size: 20px; }
  .card-front .brand-sub { font-size: 9px; letter-spacing: 6px; padding-left: 6px; margin-top: 5px; }

  .contact-bar {
    position: absolute; left: 290px; top: 118px;
    width: 30px; height: 176px; border-radius: 15px;
    background: var(--taupe);
  }
  .contact-icon {
    position: absolute; left: 3px; width: 24px; height: 24px;
  }
  .contact-list {
    position: absolute; left: 332px; top: 118px; list-style: none;
  }
  .contact-name {
    font-family: "Cinzel", serif; font-weight: 500; color: var(--ink);
    font-size: 17px; letter-spacing: 1px; line-height: 20px;
  }
  .contact-role {
    font-family: "Cinzel", serif; color: var(--ink);
    font-size: 10px; letter-spacing: 1.5px; line-height: 14px; margin-bottom: 44px;
  }
  .contact-line {
    font-family: "Arimo", sans-serif; color: var(--ink);
    font-size: 12.5px; letter-spacing: 0.8px; line-height: 20px; margin-bottom: 12px;
  }
</style>
</head>
<body>
<main class="stage">

  <section class="card card-back" aria-label="Card back">
    <div class="brand-mark"></div>
    <div class="brand-name">Talven Doroshko</div>
    <div class="brand-sub">Photography</div>
  </section>

  <section class="card card-front" aria-label="Card front">
    <div class="front-brand">
      <div class="brand-mark"></div>
      <div class="brand-name">Talven Doroshko</div>
      <div class="brand-sub">Photography</div>
    </div>

    <div class="contact-bar">
      <svg class="contact-icon" style="top:3px" viewBox="0 0 24 24" aria-hidden="true">
        <circle cx="12" cy="12" r="11" fill="var(--icon-fill)"/>
        <circle cx="12" cy="9" r="3" fill="var(--taupe)"/>
        <path d="M6.5 18c0-3 2.5-5 5.5-5s5.5 2 5.5 5z" fill="var(--taupe)"/>
      </svg>
      <svg class="contact-icon" style="top:66px" viewBox="0 0 24 24" aria-hidden="true">
        <rect x="2" y="2" width="20" height="20" rx="3" fill="var(--icon-fill)"/>
        <text x="12" y="16.5" text-anchor="middle" font-family="Arimo, sans-serif" font-size="13" fill="var(--taupe)">@</text>
      </svg>
      <svg class="contact-icon" style="top:100px" viewBox="0 0 24 24" aria-hidden="true">
        <rect x="6" y="2" width="12" height="20" rx="2" fill="var(--icon-fill)"/>
        <rect x="8" y="4.5" width="8" height="6" fill="var(--taupe)"/>
        <circle cx="12" cy="17" r="1.6" fill="var(--taupe)"/>
      </svg>
      <svg class="contact-icon" style="top:140px" viewBox="0 0 24 24" aria-hidden="true">
        <circle cx="12" cy="12" r="10" fill="var(--icon-fill)"/>
        <g fill="none" stroke="var(--taupe)" stroke-width="1.4">
          <ellipse cx="12" cy="12" rx="4" ry="8"/>
          <line x1="4" y1="12" x2="20" y2="12"/>
        </g>
      </svg>
    </div>

    <ul class="contact-list">
      <li class="contact-name">Talven Doroshko</li>
      <li class="contact-role">Owner</li>
      <li class="contact-line">07912 458203</li>
      <li class="contact-line">www.talvendoraphoto.com</li>
      <li class="contact-line">info@talvendoraphoto.com</li>
    </ul>
  </section>

</main>
</body>
</html>
```